Corporate Design für Malermeister
Zielgruppe
Ich bin Malermeister ,
wir bieten komplettrenovierungen an vom Gestalten der Oberflächen, kreative Wandgestaltung Trockenbau, Bodenverlegearbeiten Parkett, Laminat, Teppich, designböden etc.
Fokus liegt bei den Malerarbeiten! Auch Fassaden werden restaurariert und gestaltet
Wir wollen modern und hochwertig rüber kommen
Aufgabenstellung
Das Logo soll zeigen, dass wir ein moderner kreativer Betrieb sind
da wir eine Diesntaleistung anbieten sollte es auch auf Vertrauen asutrahlen

```html
<!DOCTYPE html>
<html lang="de">
<head>
<meta charset="utf-8">
<title>Farbhaus – Visitenkarte Entwurf 02</title>
<link rel="stylesheet" href="https://fonts.googleapis.com/css2?family=Roboto+Condensed:wght@300;700&family=Source+Sans+3:wght@300;400;500;600&display=swap">
<style>
  :root {
    --frame-blue: #0f71b8;
    --brand-blue: #0f6cb6;
    --ink: #1d1d1b;
    --caption: #9a9a9a;
    --sheet: #ffffff;
    --card: #f5f5f5;
  }
  * { margin: 0; padding: 0; box-sizing: border-box; }
  html, body { width: 1200px; height: 1200px; overflow: hidden; }
  body {
    background: var(--frame-blue);
    position: relative;
    font-family: "Source Sans 3", sans-serif;
  }
  .sheet {
    position: absolute;
    left: 19px; top: 19px;
    width: 1162px; height: 1162px;
    background: var(--sheet);
  }
  .spec {
    position: absolute;
    left: 0; right: 0; top: 100px;
    text-align: center;
    font-weight: 300;
    font-size: 17.5px;
    line-height: 22.6px;
    color: var(--caption);
  }
  .card {
    position: absolute;
    left: 327px; top: 271px;
    width: 543px; height: 837px;
    background: var(--card);
    box-shadow: 3px 4px 10px rgba(0,0,0,0.28);
  }
  .line { position: absolute; left: 520px; white-space: nowrap; }
  .brand-name {
    top: 512px;
    font-family: "Roboto Condensed", sans-serif;
    font-weight: 700; font-size: 68px; line-height: 68px;
    color: var(--brand-blue); letter-spacing: -0.5px;
  }
  .trade {
    top: 587px;
    font-family: "Roboto Condensed", sans-serif;
    font-weight: 700; font-size: 30px; line-height: 30px;
    color: var(--ink); letter-spacing: 0.6px;
  }
  .claim {
    top: 624px;
    font-family: "Roboto Condensed", sans-serif;
    font-weight: 300; font-size: 26px; line-height: 26px;
    color: var(--ink);
  }
  .person { top: 706px; font-weight: 600; font-size: 27px; line-height: 27px; color: var(--brand-blue); }
  .role { top: 736px; font-weight: 500; font-size: 25px; line-height: 25px; color: var(--ink); }
  .contact { font-weight: 500; font-size: 25px; line-height: 25px; color: var(--ink); }
  .contact.web { font-weight: 600; color: var(--brand-blue); }
  .street { top: 794px; }
  .city { top: 830px; }
  .phone { top: 898px; }
  .mail { top: 968px; }
  .web { top: 1003px; }
  .icon { position: absolute; fill: var(--brand-blue); }
</style>
</head>
<body>
  <div class="sheet">
    <div class="spec">
      Farbhaus<br>
      Visitenkarte Entwurf 02<br>
      Standard 85 x 55 mm<br>
      einseitig 4c&nbsp; | &nbsp;hochkant
    </div>
  </div>

  <div class="card"></div>

  <div class="line brand-name">Farbhaus</div>
  <div class="line trade">MALERMEISTERBETRIEB</div>
  <div class="line claim">Altes erhalten | Neues gestalten</div>

  <div class="line person">Jonas Berling</div>
  <div class="line role">Malermeister</div>

  <svg class="icon" style="left:481px;top:791px" width="28" height="25" viewBox="0 0 28 25" aria-hidden="true">
    <path d="M14 1 L27 12 L24 12 L24 24 L17 24 L17 16 L11 16 L11 24 L4 24 L4 12 L1 12 Z"/>
  </svg>
  <div class="line contact street">Lindenweg 14</div>
  <div class="line contact city">48231 Velden</div>

  <svg class="icon" style="left:488px;top:895px" width="14" height="25" viewBox="0 0 14 25" aria-hidden="true">
    <path d="M3 0 H11 A3 3 0 0 1 14 3 V22 A3 3 0 0 1 11 25 H3 A3 3 0 0 1 0 22 V3 A3 3 0 0 1 3 0 Z M2.5 3.5 V19 H11.5 V3.5 Z M7 20.5 A1.3 1.3 0 1 0 7 23.1 A1.3 1.3 0 1 0 7 20.5 Z"/>
  </svg>
  <div class="line contact phone">0152 - 418 27 39</div>

  <svg class="icon" style="left:480px;top:969px" width="30" height="22" viewBox="0 0 30 22" aria-hidden="true">
    <path d="M2 0 H28 A2 2 0 0 1 30 2 V3 L15 12 L0 3 V2 A2 2 0 0 1 2 0 Z M0 6 L15 15 L30 6 V20 A2 2 0 0 1 28 22 H2 A2 2 0 0 1 0 20 Z"/>
  </svg>
  <div class="line contact mail">maler@farbhaus-velden.de</div>

  <svg class="icon" style="left:482px;top:1003px" width="26" height="26" viewBox="0 0 26 26" aria-hidden="true">
    <circle cx="13" cy="13" r="12.5"/>
    <path fill="#f5f5f5" d="M7 5 C9 6 11 6 11 9 C11 11 8 11 8 13 C8 15 10 16 10 19 L8 21 C5 19 4 15 5 12 C4 10 5 7 7 5 Z M16 3 C18 5 21 6 22 9 C20 9 18 8 17 10 C16 12 19 13 19 16 C18 19 16 21 14 22 C15 19 13 17 14 14 C12 13 13 10 15 9 C14 7 14 5 16 3 Z"/>
  </svg>
  <div class="line contact web">www.farbhaus-velden.de</div>
</body>
</html>
```